Web Design Project

We are an IT System Integrator. We provide Korvin 450 ERP System, CRM etc. We also provide hardware, networking servicing. Please look at www.zolvantix.com.sg. They provide the same service as us. We like to redesign our web site. I will attached the color that I prefer for reference.

Our website is www.tadurk.com.sg.  It has been created about 14 years ago.  We are trying to revamp it with a new look and information.   The new website must be informative, fast.    I have attached an attachment which show the color that I prefer(brownish golden).   

Our competitor (www.zolvantix.com) is carrying the same trade as us.  They have all the informations In their website that we will like to have.  Therefore I recommend you to take a look at my competitor website and have a better   
understanding on the kind of information I would like to have for my new website.

This project is guarantee to the person with the best design.  We can have it guarantee.

Target Market(s)

Corporate and companies

Industry/Entity Type

Hardware

```html
<!DOCTYPE html>
<html lang="en">
<head>
<meta charset="utf-8">
<title>Nerovia Information System</title>
<link href="https://fonts.googleapis.com/css2?family=Open+Sans:wght@300;400&family=Roboto:wght@300;400;500;700&display=swap" rel="stylesheet">
<style>
:root{
  --black:#000;
  --footer:#2a2a2a;
  --accent:#1a9ad6;
  --strip:#f4f4f4;
  --card:#9aa3ab;
  --card-text:#f2f4f6;
  --heading-grey:#707a84;
  --partner-grey:#9a9a9a;
  --text:#222;
  --white:#fff;
}
*{box-sizing:border-box;margin:0;padding:0}
html,body{width:1200px;height:1178px;overflow:hidden;background:var(--white)}
body{position:relative;font-family:"Open Sans",Arial,sans-serif;color:var(--text)}
.abs{position:absolute}
.site-header{left:0;top:0;width:1200px;height:112px;background:var(--black)}
.brand{left:44px;top:68px;display:flex;align-items:center;gap:14px;color:var(--white);font:500 16px "Roboto",Arial,sans-serif}
.brand-mark{width:20px;height:20px;border:2px solid var(--white)}
.nav{right:26px;top:66px;display:flex;gap:24px}
.nav-item{display:flex;flex-direction:column;align-items:center;gap:4px;color:var(--white);font:400 8px "Roboto",Arial,sans-serif;width:32px}
.hero{left:0;top:112px;width:1200px;height:403px;background:linear-gradient(100deg,#b9c3cc 0%,#c9d0d6 35%,#d8c2ae 65%,#a88a70 100%)}
.hero-frame{left:24px;top:15px;width:1157px;height:378px;border:1px solid rgba(255,255,255,.85)}
.hero-copy{right:654px;top:86px;text-align:right;color:#fff;font-family:"Roboto",Arial,sans-serif;text-shadow:0 1px 2px rgba(0,0,0,.35)}
.hero-copy .lead{font-weight:300;font-size:20px;line-height:25px;color:#111;text-shadow:none}
.hero-copy .big{font-weight:700;font-size:25px;line-height:29px}
.hero-actions{left:296px;top:313px;display:flex;align-items:center;gap:12px;color:#fff;font:400 15px "Roboto",Arial,sans-serif}
.btn-quote{border:1px solid #fff;padding:14px 5px;width:143px;text-align:center;text-shadow:0 1px 2px rgba(0,0,0,.4)}
.or{font-size:11px;color:#222}
.learn{font-size:14px;color:#333}
.features{left:0;top:515px;width:1200px;height:102px;background:var(--strip)}
.feature{top:12px;display:flex;gap:10px}
.feature h3{font:500 17px "Roboto",Arial,sans-serif;color:var(--accent);margin-bottom:2px}
.feature p{font-size:14px;line-height:19px;color:#222}
.divider{top:10px;width:1px;height:82px;background:#d0d0d0}
.section-title{left:0;top:633px;width:1185px;text-align:center;font:300 25px "Roboto",Arial,sans-serif;color:var(--heading-grey)}
.card{top:680px;width:216px;height:196px;background:var(--card);border-radius:3px;text-align:center;color:var(--card-text);padding-top:8px}
.card h4{font:500 17px "Roboto",Arial,sans-serif;margin:6px 0 8px}
.card p{font:300 13.5px/17px "Open Sans",Arial,sans-serif;padding:0 19px;text-align:left;white-space:nowrap}
.partners{left:0;top:898px;width:1200px;height:54px;background:var(--strip);border-top:1px solid #bbb;color:var(--partner-grey);font-family:"Roboto",Arial,sans-serif}
.partner{position:absolute;white-space:nowrap}
.footer{left:0;top:952px;width:1200px;height:226px;background:var(--footer);color:var(--accent);font-family:"Roboto",Arial,sans-serif}
.fcol{top:34px}
.fcol h5{font:500 18px "Roboto",Arial,sans-serif;margin-bottom:20px}
.fcol li{list-style:none;font-size:16px;line-height:18px;white-space:nowrap}
.fcol.contact li{font-size:17px;line-height:21px}
.search{left:856px;top:30px;width:216px;height:34px;background:#e9e9e9;border:2px solid var(--accent);border-radius:2px;color:#222;font-size:12px;padding:8px 7px}
.social{left:858px;top:82px;display:flex;gap:17px}
.social i{display:block;width:32px;height:32px;border-radius:50%;background:var(--accent)}
.copyright{left:0;top:200px;width:1200px;text-align:center;color:#fff;font-size:12px}
</style>
</head>
<body>
<header class="site-header abs">
  <div class="brand abs"><span class="brand-mark"></span>Nerovia Information System</div>
  <nav class="nav abs">
    <div class="nav-item"><svg width="20" height="18" viewBox="0 0 20 18"><path d="M10 1 1 9h3v8h4v-5h4v5h4V9h3z" fill="#fff"/></svg>HOME</div>
    <div class="nav-item"><svg width="22" height="18" viewBox="0 0 22 18"><rect y="1" width="22" height="3.5" fill="#fff"/><rect y="7.2" width="22" height="3.5" fill="#fff"/><rect y="13.5" width="22" height="3.5" fill="#fff"/></svg>MENU</div>
    <div class="nav-item"><svg width="20" height="20" viewBox="0 0 20 20"><path d="M6 4.5A7.5 7.5 0 1 0 14 4.5" fill="none" stroke="#fff" stroke-width="2.4"/><line x1="10" y1="1" x2="10" y2="10" stroke="#fff" stroke-width="2.4"/></svg>LOGIN</div>
  </nav>
</header>

<section class="hero abs" role="img" aria-label="Photo of a smiling woman working at a laptop in a bright office">
  <div class="hero-frame abs"></div>
  <svg class="abs" style="left:56px;top:128px" width="36" height="170"><polyline points="33,2 3,85 33,168" fill="none" stroke="#222" stroke-width="1.2"/></svg>
  <svg class="abs" style="left:1118px;top:128px" width="36" height="170"><polyline points="3,2 33,85 3,168" fill="none" stroke="#fff" stroke-width="1.2"/></svg>
  <div class="hero-copy abs">
    <div class="lead">Organizing a business was once damned<br>Every achievement of targets was<br>considered impossible</div>
    <div class="big">But our passion is to find<br>business solutions...<br>THEN<br>NOW</div>
    <div class="big"><span style="font-weight:300">in the</span> FUTURE</div>
  </div>
  <div class="hero-actions abs"><span class="btn-quote">Get a Quote NOW</span><span class="or">or</span><span class="learn">Learn More</span></div>
</section>

<section class="features abs">
  <div class="feature abs" style="left:45px">
    <svg width="24" height="26" viewBox="0 0 24 26"><rect x="2" y="4" width="20" height="20" fill="none" stroke="#666" stroke-width="2"/><rect x="8" y="1" width="8" height="5" fill="#666"/><polyline points="7,14 11,18 18,9" fill="none" stroke="#666" stroke-width="2.4"/></svg>
    <div><h3>Korvin Certifed</h3><p>Lorem ipsum dolor sit amet,<br>consectetur adipiscing elit.</p></div>
  </div>
  <div class="divider abs" style="left:280px"></div>
  <div class="feature abs" style="left:311px">
    <svg width="26" height="26" viewBox="0 0 26 26"><rect x="1" y="11" width="6" height="13" fill="#666"/><path d="M9 11l5-9c2 0 3 1 3 3l-1 5h7c2 0 3 2 2 4l-3 8c-1 2-2 2-4 2H9z" fill="#666"/></svg>
    <div><h3>Success Stories</h3><p>Donec at malesuada lacus.<br>Donec non tempus lacus.</p></div>
  </div>
  <div class="divider abs" style="left:584px"></div>
  <div class="feature abs" style="left:602px">
    <svg width="28" height="26" viewBox="0 0 28 26"><polyline points="2,2 2,24 27,24" fill="none" stroke="#666" stroke-width="2"/><polyline points="5,20 11,12 16,16 25,5" fill="none" stroke="#666" stroke-width="2.4"/></svg>
    <div><h3>Latest VELTRA</h3><p>Donec tempus quam et elit.<br>Etiam vitae nisi mauris.</p></div>
  </div>
  <div class="divider abs" style="left:865px"></div>
  <div class="feature abs" style="left:888px">
    <svg width="28" height="26" viewBox="0 0 28 26"><rect x="2" y="4" width="24" height="14" rx="3" fill="#777"/><circle cx="14" cy="17" r="6" fill="#777" stroke="#f4f4f4" stroke-width="2"/><circle cx="14" cy="17" r="2" fill="#f4f4f4"/></svg>
    <div><h3>Services Beyond</h3><p>Integer malesuada convallis ipsum,<br>fermentum scelerisque lectus.</p></div>
  </div>
</section>

<h2 class="section-title abs">WE TAKE CARE OF ALL YOUR BUSINESS NEEDS</h2>

<article class="card abs" style="left:129px">
  <svg width="36" height="34" viewBox="0 0 36 34"><path d="M12 20l8-8 5 5-8 8c-3 3-7 3-9 1s-1-4 4-6z" fill="#fff"/><line x1="20" y1="10" x2="27" y2="3" stroke="#fff" stroke-width="3"/><line x1="26" y1="16" x2="33" y2="9" stroke="#fff" stroke-width="3"/><line x1="9" y1="26" x2="3" y2="32" stroke="#fff" stroke-width="3"/></svg>
  <h4>SOLUTIONS</h4>
  <p>Lorem ipsum dolor sit amet,<br>consectetur adipiscing elit.<br>Cras scelerisque metus nec<br>purus pharetra, ac posuere<br>orci congue. Integer aliquet<br>hendrerit ipsum vitae pulv.</p>
</article>
<article class="card abs" style="left:373px">
  <svg width="36" height="34" viewBox="0 0 36 34"><rect x="2" y="3" width="32" height="22" fill="none" stroke="#fff" stroke-width="3"/><rect x="14" y="25" width="8" height="4" fill="#fff"/><rect x="9" y="29" width="18" height="3" fill="#fff"/></svg>
  <h4>HARDWARE</h4>
  <p>Lorem ipsum dolor sit amet,<br>consectetur adipiscing elit.<br>Cras scelerisque metus nec<br>purus pharetra, ac posuere<br>orci congue. Integer aliquet<br>hendrerit ipsum vitae pulv.</p>
</article>
<article class="card abs" style="left:615px">
  <svg width="36" height="36" viewBox="0 0 36 36"><line x1="6" y1="6" x2="30" y2="30" stroke="#fff" stroke-width="5"/><line x1="30" y1="6" x2="8" y2="28" stroke="#fff" stroke-width="4"/><circle cx="29" cy="7" r="5" fill="#fff"/><circle cx="6" cy="6" r="4" fill="#fff"/></svg>
  <h4>SERVICES</h4>
  <p>Lorem ipsum dolor sit amet,<br>consectetur adipiscing elit.<br>Cras scelerisque metus nec<br>purus pharetra, ac posuere<br>orci congue. Integer aliquet<br>hendrerit ipsum vitae pulv.</p>
</article>
<article class="card abs" style="left:856px">
  <svg width="36" height="34" viewBox="0 0 36 34"><rect x="12" y="2" width="12" height="6" fill="none" stroke="#fff" stroke-width="3"/><rect x="2" y="8" width="32" height="24" fill="#fff"/><rect x="2" y="18" width="32" height="2" fill="#9aa3ab"/><rect x="15" y="16" width="6" height="6" fill="#9aa3ab"/></svg>
  <h4>CLIENTS</h4>
  <p>Lorem ipsum dolor sit amet,<br>consectetur adipiscing elit.<br>Cras scelerisque metus nec<br>purus pharetra, ac posuere<br>orci congue. Integer aliquet<br>hendrerit ipsum vitae pulv.</p>
</article>

<section class="partners abs">
  <span class="partner" style="left:259px;top:34px;font-size:8px">Partners</span>
  <span class="partner" style="left:326px;top:16px;font-size:20px;font-weight:700">Strivex</span>
  <span class="partner" style="left:456px;top:6px;width:42px;height:42px;border-radius:50%;border:2px solid #aaa"></span>
  <span class="partner" style="left:567px;top:12px;font-size:26px;font-weight:700">korvin</span>
  <span class="partner" style="left:690px;top:18px;font-size:15px">Korvin Veltra ERP</span>
  <span class="partner" style="left:834px;top:16px;font-size:18px;font-weight:700">Pelmor</span>
</section>

<footer class="footer abs">
  <div class="fcol contact abs" style="left:152px"><h5>NIS Pte Ltd</h5><ul><li>Address, City, Str</li><li>Phone: 01-555-555</li><li>Email: info@nvis.com</li></ul></div>
  <div class="fcol abs" style="left:368px"><h5>About us</h5><ul><li>Company profile</li><li>This is footer you</li><li>Can add any links</li><li>For quick navigation</li><li>And a lot of SEO</li></ul></div>
  <div class="fcol abs" style="left:552px"><h5>Help</h5><ul><li>I am a client</li><li>I am a agency</li><li>F.A.Q.</li><li>Support Department</li></ul></div>
  <div class="fcol abs" style="left:719px"><h5>Legal</h5><ul><li>Terms of Use</li><li>Privacy Policy</li></ul></div>
  <div class="search abs">search
    <svg class="abs" style="right:6px;top:4px" width="24" height="24" viewBox="0 0 24 24"><circle cx="10" cy="10" r="7" fill="none" stroke="#111" stroke-width="2.2"/><line x1="15" y1="15" x2="22" y2="22" stroke="#111" stroke-width="2.6"/></svg>
  </div>
  <div class="social abs" aria-label="Social network links"><i></i><i></i><i></i></div>
  <div class="copyright abs">© 2013 Nerovia Information Systems Pte Ltd. All rights reserved</div>
</footer>
</body>
</html>
```